NEW Wordpress Website Design for a Dynamic Long Term Healthcare Company in Hawaii

I would like a new website design for my current company, Marlow Health Collective, which has two different brands - Marlow Homecare and Marlow Senior Living. You can see the current website at www.marlowhealth-example.com. The website should be built using Wordpress Software and the Framewise theme. The website should have a local Hawaii island/tropical feel, but look professional for healthcare. I'm looking for something fresh, and want the designer to select colors, styles, etc.

In the Header, on all pages, I would like a menu that includes Home Care, Senior Living, Rates, and About Us.
Under each of the Header Menu Titles, I would like these drop downs included:
Home Care (drop down pages)- Nurse Aide Care, 24-Hour Home Care, Skilled Nursing, Lifestyle Aide, Hospice at Home, Bathing & Meal Service.
Senior Living (drop down pages) - Long-Term Stay, Short-Term Stay.
Rates (drop down page) - Rates.
About Us (drop down pages) - Our Mission, Ohana Talk, About Dana Marlow.

In the footer, on all pages, you should include the address: 248 Pueo Lane, Suite 310, Honolulu, HI 96817. Phone number: 808-555-0172
The footer should also include buttons for a page called Learn, Caregiver Jobs, and each of the service page links to include: Nurse Aide Care, 24-Hour Home Care, Skilled Nursing, Lifestyle Aide, Hospice at Home, Bathing & Meal Service.
Please don't take the current website and redesign a few aspects. I'm looking for a completely different look and feel.

Target Market(s)

40-80 year olds

Industry/Entity Type

Long Term Healthcare

Coding

Coded - Design and coding required

Requirements
Should not have
• Our existing website as a template. We are looking for a complete redesign. Thank you.

```html
<!DOCTYPE html>
<html lang="en">
<head>
<meta charset="utf-8">
<title>Marlow Health Collective – Homecare &amp; Senior Living</title>
<link rel="stylesheet" href="https://fonts.googleapis.com/css2?family=Cinzel:wght@400;600&family=Montserrat:wght@400;500;600;700&display=swap">
<style>
:root{
  --orange:#f29a1f;
  --orange-dark:#e07f10;
  --teal:#2cc3b3;
  --teal-dark:#1fa898;
  --ink:#2f2f2f;
  --text:#555;
  --sand:#fbf5ea;
  --sky:#bfe6f2;
  --sea:#3fb8cf;
  --white:#fff;
  --line:#d9d9d9;
}
*{box-sizing:border-box;margin:0;padding:0}
html,body{width:1200px;height:4456px;overflow:hidden}
body{font-family:"Montserrat",sans-serif;color:var(--text);background:var(--white);position:relative}
a{text-decoration:none;color:inherit}

/* buttons */
.btn{display:inline-flex;align-items:center;justify-content:center;gap:8px;height:40px;padding:0 26px;border-radius:20px;font-size:13px;font-weight:700;letter-spacing:.06em;text-transform:uppercase;color:var(--white);white-space:nowrap}
.btn-orange{background:var(--orange)}
.btn-teal{background:var(--teal)}
.btn::after{content:"›";font-size:18px;line-height:1}

/* header */
.site-header{position:absolute;top:0;left:0;width:1200px;height:90px;z-index:20;display:flex;align-items:center;padding:0 112px}
.brand{display:flex;align-items:center;gap:10px;font-weight:700;font-size:22px;color:var(--orange);white-space:nowrap}
.brand-mark{width:26px;height:26px;background:var(--orange);border-radius:6px}
.main-nav{display:flex;gap:38px;margin-left:auto;font-size:13px;font-weight:600;letter-spacing:.06em;color:var(--ink);text-transform:uppercase;white-space:nowrap}
.main-nav span::after{content:" ⌄";color:var(--orange)}
.main-nav span.no-drop::after{content:none}
.header-phone{display:flex;align-items:center;gap:10px;margin-left:44px;font-weight:700;font-size:18px;color:var(--ink);white-space:nowrap}
.icon-dot{width:30px;height:30px;border-radius:50%;background:var(--orange);display:flex;align-items:center;justify-content:center}

/* hero */
.hero{position:absolute;top:0;left:0;width:1200px;height:800px;overflow:hidden;z-index:1;background:linear-gradient(180deg,#eaf7fb 0%,#d6f0f6 40%,var(--sky) 62%,var(--sea) 78%,#7fd3de 100%)}
.hero-palm-left{position:absolute;left:0;top:0;width:230px;height:520px;background:radial-gradient(ellipse at 0 40%,rgba(90,140,70,.45),rgba(90,140,70,0) 70%)}
.hero-palm-right{position:absolute;right:0;top:160px;width:260px;height:560px;background:radial-gradient(ellipse at 100% 40%,rgba(90,140,70,.5),rgba(90,140,70,0) 70%)}
.hero-copy{position:absolute;left:118px;top:258px}
.hero-eyebrow{font-size:15px;font-weight:600;letter-spacing:.12em;color:var(--ink);text-transform:uppercase}
.hero-title{font-family:"Cinzel",serif;font-size:62px;line-height:66px;font-weight:400;color:var(--orange);margin-top:10px}
.hero-actions{display:flex;gap:18px;margin-top:38px}
.hero-photo{position:absolute;left:616px;top:100px;width:420px;height:420px;border-radius:50%;border:10px solid var(--orange);background:linear-gradient(135deg,#c79a6a,#8a5a3a 55%,#d9b48a)}
.hero-wave{position:absolute;left:0;bottom:0}

/* mission */
.mission-photo{position:absolute;left:116px;top:812px;width:390px;height:390px;border-radius:50%;border:10px solid var(--teal);background:linear-gradient(160deg,#6ca36a,#3f7f52 50%,#a9c98c)}
.mission-portrait{position:absolute;left:300px;top:1080px;width:200px;height:200px;border-radius:50%;border:8px solid var(--white);background:linear-gradient(160deg,#6fb3c9,#3d8aa3);box-shadow:0 6px 18px rgba(0,0,0,.15)}
.mission-copy{position:absolute;left:620px;top:868px;width:450px}
.section-title{font-family:"Cinzel",serif;font-weight:400;font-size:46px;color:var(--ink);letter-spacing:.02em;white-space:nowrap}
.title-rule{width:70px;height:3px;background:var(--orange);margin:10px 0 24px}
.body-text{font-size:15px;line-height:26px;color:var(--text)}
.mission-copy .btn{margin-top:26px}

/* home care */
.homecare{position:absolute;top:1300px;left:0;width:1200px;height:400px;background:linear-gradient(180deg,var(--white),var(--sand))}
.homecare-head{text-align:center;margin-top:72px}
.homecare-head .title-rule{margin:10px auto 24px}
.homecare-head .body-text{width:700px;margin:0 auto}
.service-list{display:grid;grid-template-columns:250px 230px 230px;row-gap:18px;justify-content:center;margin:34px auto 0;font-size:13px;font-weight:600;color:var(--ink);text-transform:uppercase;letter-spacing:.03em}
.service-list li{list-style:none;display:flex;align-items:center;gap:10px;white-space:nowrap}
.service-list li.is-active{border:2px solid var(--orange);padding:6px 10px;margin:-8px 0 0 -12px;width:200px}
.homecare .btn{display:flex;width:170px;margin:28px auto 0}
.homecare-photo{position:absolute;top:1700px;left:0;width:1200px;height:390px;background:linear-gradient(90deg,#8b6a4a,#c9a57c 30%,#e5d4b5 60%,#b48f68)}

/* senior living */
.senior{position:absolute;top:2110px;left:0;width:1200px;height:560px;background:var(--white)}
.senior-copy{position:absolute;left:118px;top:86px;width:420px}
.senior-list{list-style:none;margin-top:22px;font-size:13px;font-weight:700;color:var(--ink);letter-spacing:.04em;text-transform:uppercase}
.senior-list li{margin-bottom:10px}
.senior-list li::before{content:"› ";color:var(--orange);font-size:16px}
.senior-copy .btn{margin-top:22px}
.senior-accent{position:absolute;left:570px;top:60px;width:90px;height:90px;background:var(--orange);border-radius:18px}
.senior-photo{position:absolute;left:600px;top:80px;width:560px;height:390px;border-radius:0 40px 0 40px;background:linear-gradient(135deg,#e6d98a,#c9b25c 45%,#88a9b6)}
.leaf-right{position:absolute;right:0;top:2150px;width:90px;height:140px;background:radial-gradient(ellipse at 100% 50%,rgba(80,140,70,.5),rgba(80,140,70,0) 70%)}

/* rates */
.rates{position:absolute;top:2660px;left:0;width:1200px;height:500px;background:var(--sand)}
.rates-photo{position:absolute;left:0;top:0;width:640px;height:500px;background:linear-gradient(135deg,#8a4f2e,#c98e5f 45%,#e7cfae)}
.rates-panel{position:absolute;left:600px;top:0;width:600px;height:500px;background:linear-gradient(90deg,rgba(255,255,255,.92),rgba(255,250,240,.96));border-radius:60px 0 0 0;padding:96px 80px 0 60px}
.rates-panel .btn{margin-top:26px}

/* contact */
.contact{position:absolute;top:3200px;left:0;width:1200px;height:800px;background:linear-gradient(180deg,#d7eef5 0%,#a9dced 35%,var(--sea) 62%,#8fd6df 78%,#efe3c9 100%)}
.contact-palm{position:absolute;left:0;top:0;width:260px;height:520px;background:radial-gradient(ellipse at 0 30%,rgba(70,130,70,.55),rgba(70,130,70,0) 70%)}
.contact-form{position:absolute;left:200px;top:180px;width:860px;height:560px;background:rgba(255,255,255,.88);border-radius:26px;padding:54px 80px 0}
.form-title{font-family:"Cinzel",serif;font-weight:600;font-size:34px;line-height:42px;text-align:center;color:var(--ink)}
.form-grid{display:grid;grid-template-columns:1fr 1fr;gap:14px 16px;margin-top:34px}
.field{height:46px;border:1px solid var(--line);background:var(--white);border-radius:4px;font-size:13px;color:#777;padding:14px}
.field.wide{grid-column:1/3;height:106px}
.contact-form .btn{display:flex;width:230px;margin:28px auto 0}
.contact-form .btn::after{content:none}

/* footer */
.site-footer{position:absolute;top:4000px;left:0;width:1200px;height:456px;background:var(--white);border-top:4px solid var(--teal)}
.footer-brand{position:absolute;left:112px;top:50px;width:200px}
.footer-brand .brand{font-size:18px}
.footer-btn{display:flex;width:180px;height:34px;font-size:12px;margin-top:14px}
.footer-btn::after{content:none}
.socials{display:flex;gap:8px;margin-top:16px}
.socials span{width:26px;height:26px;border-radius:50%;background:var(--teal)}
.footer-col{position:absolute;top:80px}
.footer-col h4{font-size:17px;font-weight:600;color:var(--ink);border-left:3px solid var(--orange);padding-left:10px;margin-bottom:14px}
.footer-col ul{list-style:none;font-size:14px;line-height:26px;color:var(--text)}
.contact-item{display:flex;gap:12px;font-size:14px;line-height:20px;margin-bottom:14px;color:var(--text)}
.contact-item .icon-dot{background:var(--teal);flex:none}
.contact-item strong{color:var(--ink)}
.footer-brands{position:absolute;left:830px;top:290px;display:flex;gap:26px;font-weight:700;font-size:15px;color:var(--orange)}
.footer-brands span+span{color:var(--teal)}
.copyright{position:absolute;left:0;top:402px;width:1200px;text-align:center;font-size:12px;color:#777}
.copyright b{color:var(--orange);font-weight:600}
</style>
</head>
<body>

<header class="site-header">
  <a class="brand" href="#"><span class="brand-mark"></span>Marlow</a>
  <nav class="main-nav"><span>Home Care</span><span>Senior Living</span><span>Rates</span><span>About Us</span></nav>
  <div class="header-phone">
    <span class="icon-dot"><svg width="14" height="14" viewBox="0 0 24 24" fill="#fff"><path d="M6.6 10.8a15 15 0 0 0 6.6 6.6l2.2-2.2a1 1 0 0 1 1-.25 11.4 11.4 0 0 0 3.6.57 1 1 0 0 1 1 1V20a1 1 0 0 1-1 1A17 17 0 0 1 3 4a1 1 0 0 1 1-1h3.5a1 1 0 0 1 1 1c0 1.25.2 2.45.57 3.57a1 1 0 0 1-.25 1z"/></svg></span>
    808-555-0172
  </div>
</header>

<section class="hero">
  <div class="hero-palm-left"></div>
  <div class="hero-palm-right"></div>
  <div class="hero-copy">
    <p class="hero-eyebrow">Marlow Health Collective</p>
    <h1 class="hero-title">Homecare &amp;<br>Senior Living</h1>
    <div class="hero-actions">
      <a class="btn btn-orange" href="#">View Rates</a>
      <a class="btn btn-teal" href="#">Contact Us</a>
    </div>
  </div>
  <div class="hero-photo" role="img" aria-label="Photo of a caregiver serving a meal to seniors at a dining table"></div>
  <svg class="hero-wave" width="1200" height="180" viewBox="0 0 1200 180" aria-hidden="true">
    <path d="M0 90 C300 10 600 170 900 90 S1150 40 1200 60 V180 H0Z" fill="var(--orange)" opacity=".9"/>
    <path d="M0 110 C300 30 600 190 900 110 S1150 60 1200 80 V180 H0Z" fill="#fff"/>
  </svg>
</section>

<section class="mission">
  <div class="mission-photo" role="img" aria-label="Photo of a caregiver helping a senior walk with a walker in a garden"></div>
  <div class="mission-portrait" role="img" aria-label="Portrait photo of the founder"></div>
  <div class="mission-copy">
    <h2 class="section-title">Our Mission</h2>
    <div class="title-rule"></div>
    <p class="body-text">At Marlow Health Collective, our mission is to provide compassionate and professional long-term healthcare services that empower individuals to maintain their highest level of independence, health, and well-being in the comfort of their own homes or ours, either through our licensed home healthcare agency</p>
    <a class="btn btn-orange" href="#">Learn More</a>
  </div>
</section>

<section class="homecare">
  <div class="homecare-head">
    <h2 class="section-title">Home Care</h2>
    <div class="title-rule"></div>
    <p class="body-text">Marlow Homecare understands that every person's care journey is unique. We tailor our in-home services to meet the diverse nurturing experience</p>
  </div>
  <ul class="service-list">
    <li class="is-active"><svg width="14" height="12" viewBox="0 0 14 12"><path d="M1 6l4 4 8-9" stroke="var(--orange)" stroke-width="2.5" fill="none"/></svg>Nurse Aide Care</li>
    <li><svg width="14" height="12" viewBox="0 0 14 12"><path d="M1 6l4 4 8-9" stroke="var(--orange)" stroke-width="2.5" fill="none"/></svg>Lifestyle Aide</li>
    <li><svg width="14" height="12" viewBox="0 0 14 12"><path d="M1 6l4 4 8-9" stroke="var(--orange)" stroke-width="2.5" fill="none"/></svg>Bathing &amp; Meal Service</li>
    <li><svg width="14" height="12" viewBox="0 0 14 12"><path d="M1 6l4 4 8-9" stroke="var(--orange)" stroke-width="2.5" fill="none"/></svg>24-Hour Home Care</li>
    <li><svg width="14" height="12" viewBox="0 0 14 12"><path d="M1 6l4 4 8-9" stroke="var(--orange)" stroke-width="2.5" fill="none"/></svg>Hospice at Home</li>
    <li><svg width="14" height="12" viewBox="0 0 14 12"><path d="M1 6l4 4 8-9" stroke="var(--orange)" stroke-width="2.5" fill="none"/></svg>Skilled Nursing</li>
  </ul>
  <a class="btn btn-teal" href="#">Learn More</a>
</section>
<div class="homecare-photo" role="img" aria-label="Photo of caregivers and seniors knitting together on a sofa in a living room"></div>

<section class="senior">
  <div class="senior-copy">
    <h2 class="section-title">Senior Living</h2>
    <div class="title-rule"></div>
    <p class="body-text">Marlow Senior Living creates a warm, supportive, and enriching care home environment where seniors can thrive in their golden years. We provide residential care that promotes well-being, connection, and dignity of each individual.</p>
    <ul class="senior-list"><li>Long-Term Stay</li><li>Short-Term Stay</li></ul>
    <a class="btn btn-teal" href="#">Learn More</a>
  </div>
  <div class="senior-accent"></div>
  <div class="senior-photo" role="img" aria-label="Photo of a caregiver assisting a senior resident in a bright bedroom"></div>
</section>
<div class="leaf-right"></div>

<section class="rates">
  <div class="rates-photo" role="img" aria-label="Photo of a caregiver serving lunch to seniors in a dining room"></div>
  <div class="rates-panel">
    <h2 class="section-title">Rate &amp; Prices</h2>
    <div class="title-rule"></div>
    <p class="body-text">At Marlow Health Collective, our mission is to provide compassionate and professional long-term healthcare services that empower individuals to maintain their highest level of independence, health, and well-being in the comfort of their own homes or ours, either through our licensed home healthcare agency</p>
    <a class="btn btn-orange" href="#">Learn More</a>
  </div>
</section>

<section class="contact" role="img" aria-label="Tropical beach with palm trees and turquoise sea">
  <div class="contact-palm"></div>
  <form class="contact-form">
    <h2 class="form-title">Schedule a Complimentary<br>Care Consultation</h2>
    <div class="form-grid">
      <div class="field">First Name</div>
      <div class="field">Last Name</div>
      <div class="field">Email address</div>
      <div class="field">Phone Number</div>
      <div class="field wide">Message</div>
    </div>
    <a class="btn btn-teal" href="#">Send Message</a>
  </form>
</section>

<footer class="site-footer">
  <div class="footer-brand">
    <a class="brand" href="#"><span class="brand-mark"></span>Marlow</a>
    <a class="btn btn-teal footer-btn" href="#">Learn</a>
    <a class="btn btn-orange footer-btn" href="#">Caregiver Jobs</a>
    <div class="socials"><span></span><span></span><span></span><span></span></div>
  </div>
  <div class="footer-col" style="left:384px">
    <h4>Navigation</h4>
    <ul><li>Home Care</li><li>Senior Living</li><li>Rates</li><li>About Us</li></ul>
  </div>
  <div class="footer-col" style="left:592px">
    <h4>Services</h4>
    <ul><li>Nurse Aide Care</li><li>24-Hour Home Care</li><li>Skilled Nursing</li><li>Lifestyle Aide</li><li>Hospice at Home</li><li>Bathing &amp; Meal Service</li></ul>
  </div>
  <div class="footer-col" style="left:820px">
    <h4>Contact Us</h4>
    <div class="contact-item">
      <span class="icon-dot"><svg width="12" height="14" viewBox="0 0 24 28" fill="#fff"><path d="M12 0a10 10 0 0 0-10 10c0 7.5 10 18 10 18s10-10.5 10-18A10 10 0 0 0 12 0zm0 14a4 4 0 1 1 0-8 4 4 0 0 1 0 8z"/></svg></span>
      <span>248 Pueo Lane, Suite 310,<br>Honolulu, HI 96817</span>
    </div>
    <div class="contact-item">
      <span class="icon-dot"><svg width="13" height="13" viewBox="0 0 24 24" fill="#fff"><path d="M6.6 10.8a15 15 0 0 0 6.6 6.6l2.2-2.2a1 1 0 0 1 1-.25 11.4 11.4 0 0 0 3.6.57 1 1 0 0 1 1 1V20a1 1 0 0 1-1 1A17 17 0 0 1 3 4a1 1 0 0 1 1-1h3.5a1 1 0 0 1 1 1c0 1.25.2 2.45.57 3.57a1 1 0 0 1-.25 1z"/></svg></span>
      <span>Phone number<br><strong>808-555-0172</strong></span>
    </div>
  </div>
  <div class="footer-brands"><span>Marlow Homecare</span><span>Marlow Senior Living</span></div>
  <p class="copyright">Copyright © 2024 <b>Marlow Health Collective</b>. All Right Reserved</p>
</footer>

</body>
</html>
```